Modern Label for cleaning products for the brand Vorlix

We need a label design for our line of cleaning products. The label should feature our logo and an image to identify the product's intended use. I've added our logo and an image for use. This only concerns the design of the label on the front of the bottle.

Label dimensions:
Label 1 (500ml bottle with spray): width 58mm x height 115mm
Label 2: (1L bottle): width 73mm x height 140mm
The design must be consistent for both bottles which you find in the pictures.

The bottles to be labeled are white. See the attachment for a photo of the bottles.

The photo must also appear on the label to identify the product's intended use.

Product information:
Brand: Vorlix
Product: Sanitary Cleaner

This text must be placed on the label:
"Cleans, descales & freshens. followed with this text: "Ideal for quick and powerful cleaning. A ready-to-use product for everyday use."

- Mention the seperate USP's: Sanitary, Bathroom, Toilet, Wet areas

Appearance: This is a consumer product, but it must have a professional appearance. We would like to see a design that use the color blue from our logo.

Target Market(s)

Consumers who take care of their homes and want to maintain it the correct (professional) way

Font styles to use
Sans Serif

Colors
0054AA
0677BA
7BADD7
CADEEF
E8F1F8

Requirements
Must have
• USP's + use of image and logo + blend in 1 design
Nice to have
• Keep the color of the logo in the design
Should not have
• Comic sans

```html
<!DOCTYPE html>
<html lang="en">
<head>
<meta charset="utf-8">
<title>Vorlix Sanitary Cleaner – Label Sizes</title>
<link rel="stylesheet" href="https://fonts.googleapis.com/css2?family=Montserrat:wght@400;500;600;700;800&family=Arimo:wght@400&display=swap">
<style>
  :root{
    --brand-deep:#0054AA;
    --brand-blue:#0a86cc;
    --brand-mid:#7BADD7;
    --brand-light:#CADEEF;
    --brand-pale:#E8F1F8;
    --ink:#1d1d1b;
    --tick:#f39200;
    --dim:#2f6ea8;
    --board-center:#fdfef2;
    --board-edge:#dbe58c;
  }
  *{margin:0;padding:0;box-sizing:border-box}
  html,body{width:1200px;height:1200px;overflow:hidden}
  body{
    position:relative;
    background:radial-gradient(circle at 50% 50%, var(--board-center) 0%, #eef4cf 45%, var(--board-edge) 100%);
    font-family:"Montserrat",sans-serif;
  }
  .abs{position:absolute}
  .center-line{position:absolute;left:0;right:0;text-align:center;white-space:nowrap}

  /* brand header */
  .brand-header{left:190px;top:130px;width:310px;height:170px}
  .brand-header .brand-dot{position:absolute;left:105px;top:8px;width:100px;height:100px;border-radius:50%;border:14px solid var(--brand-blue)}
  .brand-header .brand-name{top:118px;font-size:46px;line-height:56px;font-weight:700;color:var(--ink)}

  /* dimension layer */
  .dimensions{position:absolute;left:0;top:0;width:1200px;height:1200px}
  .dim-text{font-family:"Arimo",sans-serif;fill:var(--dim)}

  /* label */
  .label{
    position:absolute;overflow:hidden;
    background:linear-gradient(180deg,#ffffff 0%, var(--brand-pale) 30%, #c6e6f8 70%, #a4d7f4 100%);
    color:var(--brand-blue);
  }
  .label--small{left:193px;top:495px;width:302px;height:599px}
  .label--large{left:673px;top:365px;width:380px;height:730px}

  .label .brand-dot{position:absolute;border-radius:50%;border-style:solid;border-color:var(--brand-blue)}
  .label .brand-name{font-weight:700;color:var(--ink)}
  .product-title{font-weight:800;letter-spacing:-0.5px;color:var(--brand-blue)}
  .product-sub{font-weight:600;letter-spacing:1px;color:var(--brand-blue)}

  .benefits{position:absolute;list-style:none}
  .benefits li{position:absolute;left:0;white-space:nowrap;font-weight:600;display:flex;align-items:center}
  .benefits svg{flex:none}

  .seal{position:absolute;border-radius:50%;background:#fff;border:2px solid var(--ink)}
  .seal::after{content:"";position:absolute;border-radius:50%;background:var(--brand-blue)}

  .tagline{font-weight:600}
  .usage-photo{position:absolute;background:linear-gradient(100deg,#8a8a88 0%,#b7b7b5 25%,#eeeeee 45%,#f6f6f6 70%,#c9c9c7 88%,#8f8f8d 100%)}
  .usage-photo::after{content:"";position:absolute;left:0;right:0;bottom:0;height:26%;background:linear-gradient(180deg,#a9a7a4,#8c8a87)}
  .statement{font-weight:400}
  .volume{font-weight:700}

  /* small label metrics */
  .label--small .brand-dot{left:128px;top:27px;width:52px;height:52px;border-width:8px}
  .label--small .brand-name{top:79px;font-size:23px;line-height:28px}
  .label--small .product-title{top:130px;font-size:43px;line-height:50px}
  .label--small .product-sub{top:170px;font-size:33px;line-height:38px}
  .label--small .benefits{left:34px;top:0}
  .label--small .benefits li{font-size:20px;line-height:24px;gap:8px}
  .label--small .benefits li:nth-child(1){top:226px}
  .label--small .benefits li:nth-child(2){top:249px}
  .label--small .benefits li:nth-child(3){top:272px}
  .label--small .seal{left:195px;top:224px;width:72px;height:72px}
  .label--small .seal::after{left:10px;top:10px;width:48px;height:48px}
  .label--small .tagline{font-size:11px;line-height:14px}
  .label--small .tagline.l1{top:300px}
  .label--small .tagline.l2{top:314px}
  .label--small .usage-photo{left:35px;top:341px;width:232px;height:147px}
  .label--small .statement{font-size:12px;line-height:16px}
  .label--small .statement.l1{top:501px}
  .label--small .statement.l2{top:517px}
  .label--small .statement.l3{top:533px}
  .label--small .volume{top:562px;font-size:20px;line-height:24px}

  /* large label metrics */
  .label--large .brand-dot{left:162px;top:21px;width:64px;height:64px;border-width:10px}
  .label--large .brand-name{top:84px;font-size:28px;line-height:32px}
  .label--large .product-title{top:143px;font-size:54px;line-height:62px}
  .label--large .product-sub{top:192px;font-size:41px;line-height:48px}
  .label--large .benefits{left:48px;top:0}
  .label--large .benefits li{font-size:24px;line-height:28px;gap:10px}
  .label--large .benefits li:nth-child(1){top:268px}
  .label--large .benefits li:nth-child(2){top:295px}
  .label--large .benefits li:nth-child(3){top:323px}
  .label--large .seal{left:243px;top:262px;width:90px;height:90px}
  .label--large .seal::after{left:13px;top:13px;width:60px;height:60px}
  .label--large .tagline{font-size:13.5px;line-height:17px}
  .label--large .tagline.l1{top:357px}
  .label--large .tagline.l2{top:374px}
  .label--large .usage-photo{left:47px;top:407px;width:286px;height:180px}
  .label--large .statement{font-size:14.5px;line-height:19px}
  .label--large .statement.l1{top:603px}
  .label--large .statement.l2{top:623px}
  .label--large .statement.l3{top:642px}
  .label--large .volume{top:692px;font-size:21px;line-height:26px}
</style>
</head>
<body>

<header class="brand-header abs">
  <span class="brand-dot"></span>
  <div class="brand-name center-line">Vorlix</div>
</header>

<svg class="dimensions" viewBox="0 0 1200 1200" aria-hidden="true">
  <defs>
    <marker id="arrow" viewBox="0 0 10 10" refX="10" refY="5" markerWidth="7" markerHeight="7" orient="auto-start-reverse">
      <path d="M0,1 L10,5 L0,9 z" fill="#2f6ea8"/>
    </marker>
  </defs>
  <g stroke="#2f6ea8" stroke-width="1.2" fill="none">
    <!-- small label width -->
    <line x1="193" y1="453" x2="193" y2="484"/>
    <line x1="494" y1="453" x2="494" y2="484"/>
    <line x1="194" y1="466" x2="262" y2="466" marker-start="url(#arrow)"/>
    <line x1="428" y1="466" x2="493" y2="466" marker-end="url(#arrow)"/>
    <!-- small label height -->
    <line x1="147" y1="495" x2="187" y2="495"/>
    <line x1="147" y1="1094" x2="187" y2="1094"/>
    <line x1="160" y1="496" x2="160" y2="705" marker-start="url(#arrow)"/>
    <line x1="160" y1="875" x2="160" y2="1093" marker-end="url(#arrow)"/>
    <!-- large label width -->
    <line x1="673" y1="323" x2="673" y2="354"/>
    <line x1="1053" y1="323" x2="1053" y2="354"/>
    <line x1="674" y1="336" x2="780" y2="336" marker-start="url(#arrow)"/>
    <line x1="947" y1="336" x2="1052" y2="336" marker-end="url(#arrow)"/>
    <!-- large label height -->
    <line x1="621" y1="365" x2="661" y2="365"/>
    <line x1="621" y1="1094" x2="661" y2="1094"/>
    <line x1="633" y1="366" x2="633" y2="635" marker-start="url(#arrow)"/>
    <line x1="633" y1="818" x2="633" y2="1093" marker-end="url(#arrow)"/>
  </g>
  <text class="dim-text" x="345" y="478" font-size="32" text-anchor="middle">58.00 mm</text>
  <text class="dim-text" x="865" y="348" font-size="32" text-anchor="middle">73.00 mm</text>
  <text class="dim-text" transform="translate(172 790) rotate(-90)" font-size="32" text-anchor="middle">115.00 mm</text>
  <text class="dim-text" transform="translate(645 727) rotate(-90)" font-size="32" text-anchor="middle">140.00 mm</text>
</svg>

<!-- 500 ml label -->
<section class="label label--small">
  <span class="brand-dot"></span>
  <div class="brand-name center-line">Vorlix</div>
  <h1 class="product-title center-line">SANITARY</h1>
  <h2 class="product-sub center-line">CLEANER</h2>
  <ul class="benefits">
    <li><svg width="13" height="13" viewBox="0 0 14 14"><circle cx="7" cy="7" r="5.6" fill="none" stroke="#f39200" stroke-width="1.5"/><path d="M4.2 7.2 L6.4 9.3 L12 3" fill="none" stroke="#f39200" stroke-width="1.8" stroke-linecap="round"/></svg>Cleans</li>
    <li><svg width="13" height="13" viewBox="0 0 14 14"><circle cx="7" cy="7" r="5.6" fill="none" stroke="#f39200" stroke-width="1.5"/><path d="M4.2 7.2 L6.4 9.3 L12 3" fill="none" stroke="#f39200" stroke-width="1.8" stroke-linecap="round"/></svg>Descales</li>
    <li><svg width="13" height="13" viewBox="0 0 14 14"><circle cx="7" cy="7" r="5.6" fill="none" stroke="#f39200" stroke-width="1.5"/><path d="M4.2 7.2 L6.4 9.3 L12 3" fill="none" stroke="#f39200" stroke-width="1.8" stroke-linecap="round"/></svg>Freshens</li>
  </ul>
  <div class="seal" aria-hidden="true"></div>
  <p class="tagline center-line l1">Ideal for quick and powerful cleaning.</p>
  <p class="tagline center-line l2">A ready-to-use product for everyday use</p>
  <div class="usage-photo" role="img" aria-label="Photo of a modern bathroom with glass shower, washbasin and tiled bath"></div>
  <p class="statement center-line l1">We use 100% certified organic cleaners,</p>
  <p class="statement center-line l2">ensuring a safe working environment free</p>
  <p class="statement center-line l3">of harmful chemicals.</p>
  <p class="volume center-line">500ml</p>
</section>

<!-- 1 L label -->
<section class="label label--large">
  <span class="brand-dot"></span>
  <div class="brand-name center-line">Vorlix</div>
  <h1 class="product-title center-line">SANITARY</h1>
  <h2 class="product-sub center-line">CLEANER</h2>
  <ul class="benefits">
    <li><svg width="16" height="16" viewBox="0 0 14 14"><circle cx="7" cy="7" r="5.6" fill="none" stroke="#f39200" stroke-width="1.5"/><path d="M4.2 7.2 L6.4 9.3 L12 3" fill="none" stroke="#f39200" stroke-width="1.8" stroke-linecap="round"/></svg>Cleans</li>
    <li><svg width="16" height="16" viewBox="0 0 14 14"><circle cx="7" cy="7" r="5.6" fill="none" stroke="#f39200" stroke-width="1.5"/><path d="M4.2 7.2 L6.4 9.3 L12 3" fill="none" stroke="#f39200" stroke-width="1.8" stroke-linecap="round"/></svg>Descales</li>
    <li><svg width="16" height="16" viewBox="0 0 14 14"><circle cx="7" cy="7" r="5.6" fill="none" stroke="#f39200" stroke-width="1.5"/><path d="M4.2 7.2 L6.4 9.3 L12 3" fill="none" stroke="#f39200" stroke-width="1.8" stroke-linecap="round"/></svg>Freshens</li>
  </ul>
  <div class="seal" aria-hidden="true"></div>
  <p class="tagline center-line l1">Ideal for quick and powerful cleaning.</p>
  <p class="tagline center-line l2">A ready-to-use product for everyday use</p>
  <div class="usage-photo" role="img" aria-label="Photo of a modern bathroom with glass shower, washbasin and tiled bath"></div>
  <p class="statement center-line l1">We use 100% certified organic cleaners,</p>
  <p class="statement center-line l2">ensuring a safe working environment free</p>
  <p class="statement center-line l3">of harmful chemicals.</p>
  <p class="volume center-line">1.000ml</p>
</section>

</body>
</html>
```